Dental Practice Billboard Design

We are a newer dental practice in need of a simple but appealing billboard for our growing dental practice to attract new patients. The practice is owned by husband and wife dentists and is family friendly in a small town in Kentucky. We try to be very friendly and caring to our patients. Would prefer a blue background for the billboard and our tooth logo to be prominent. We are partial to the Patua One font used in the image below but please feel free to tweak it as you deem necessary. The shape of the uppercase D and lowercase g are why we like that font, so fonts with a similarly shaped “D” and “g” would work as well. Please include our phone number (555) 847-1390. Please see our website Harlowbrookdentistry.example for more info on the practice if needed. Thank you! Looking forward to seeing your creation.
Updates

The dimensions will be 12ft x 24ft (3.6576m x 7.3152m). Apologies for not including this in the original prompt. Thank you all for your submissions.

Industry/Entity Type

Dental

Font styles to use
Other font styles liked:
• Patua One

Colors
0054AA
0677BA
7BADD7
CADEEF
E8F1F8
0094D4
00A9DD
6FCCEA
C7EBF8
E9F6FB
00AB8E
00BBA5
67D7C9
C6EFE9
E9F9F6
59FF00
82FF00
B8FF75
E3FFCB
F4FFEA

Requirements
Must have
• Phone number, website, Logo, Practice name “Harlow Brook Dentistry”
Should not have
• A tagline or slogan

```html
<!DOCTYPE html>
<html lang="en">
<head>
<meta charset="utf-8">
<title>Harlow Brook Dentistry – Billboard</title>
<link rel="stylesheet" href="https://fonts.googleapis.com/css2?family=Patua+One&family=Montserrat:wght@500;700&display=swap">
<style>
  :root {
    --page: #ffffff;
    --blue-deep: #0047a0;
    --blue: #0054aa;
    --blue-light: #0677ba;
    --green: #3fae2a;
    --white: #ffffff;
    --ink: #1d2a44;
  }
  * { margin: 0; padding: 0; box-sizing: border-box; }
  html, body {
    width: 1097px;
    height: 1200px;
    overflow: hidden;
    background: var(--page);
  }
  .billboard {
    position: absolute;
    left: 30px;
    top: 341px;
    width: 1037px;
    height: 518px;
    overflow: hidden;
    background:
      linear-gradient(100deg, rgba(255,255,255,0.06) 0%, rgba(255,255,255,0) 40%),
      radial-gradient(ellipse at 60% 45%, var(--blue-light) 0%, var(--blue) 45%, var(--blue-deep) 100%);
    font-family: "Patua One", Georgia, serif;
    color: var(--white);
  }
  .clinic-backdrop {
    position: absolute;
    inset: 0;
    background: linear-gradient(180deg, rgba(120,170,220,0.10) 0%, rgba(0,40,110,0.18) 100%);
  }
  .practice-name {
    position: absolute;
    left: 62px;
    top: 62px;
    display: flex;
    align-items: center;
    gap: 16px;
  }
  .practice-name .mark {
    width: 46px;
    height: 46px;
    border-radius: 50%;
    background: var(--green);
    flex: none;
  }
  .practice-name .name {
    font-size: 36px;
    line-height: 1.05;
    color: var(--white);
  }
  .family-photo {
    position: absolute;
    left: 40px;
    top: 162px;
    width: 390px;
    height: 356px;
    background: linear-gradient(160deg, #c9a98a 0%, #a9c4dc 45%, #b33a3f 80%, #2c3140 100%);
    opacity: 0.85;
    border-radius: 4px 4px 0 0;
  }
  .message {
    position: absolute;
    left: 438px;
    top: 52px;
    width: 540px;
  }
  .pill-headline {
    height: 50px;
    border-radius: 25px;
    background: var(--green);
    display: flex;
    align-items: center;
    justify-content: center;
    font-size: 34px;
    letter-spacing: 13px;
    padding-left: 13px;
  }
  .headline {
    margin-top: 6px;
    font-size: 96px;
    line-height: 1;
    letter-spacing: -1px;
    white-space: nowrap;
  }
  .subhead {
    margin-top: 10px;
    font-size: 38px;
    letter-spacing: 11.5px;
    line-height: 1;
    white-space: nowrap;
  }
  .feature-pill {
    margin-top: 20px;
    height: 38px;
    border-radius: 19px;
    background: var(--white);
    display: flex;
    align-items: center;
    font-family: "Montserrat", Arial, sans-serif;
    font-size: 20px;
    overflow: hidden;
  }
  .feature-pill .lead {
    color: var(--ink);
    font-weight: 500;
    padding: 0 8px 0 16px;
    white-space: nowrap;
  }
  .feature-pill .highlight {
    flex: 1;
    height: 100%;
    background: var(--green);
    color: var(--white);
    font-weight: 700;
    border-radius: 19px;
    display: flex;
    align-items: center;
    justify-content: center;
    white-space: nowrap;
  }
  .phone {
    margin-top: 26px;
    font-size: 84px;
    line-height: 1;
    letter-spacing: -1px;
    white-space: nowrap;
  }
  .website {
    margin-top: 16px;
    font-size: 31px;
    line-height: 1;
    white-space: nowrap;
  }
</style>
</head>
<body>
  <section class="billboard">
    <div class="clinic-backdrop" role="img" aria-label="Softly blurred photo of a modern dental treatment room tinted blue"></div>

    <div class="practice-name">
      <span class="mark"></span>
      <span class="name">Harlow Brook<br>Dentistry</span>
    </div>

    <div class="family-photo" role="img" aria-label="Photo of a smiling family of three pointing toward the message"></div>

    <div class="message">
      <div class="pill-headline">COMPREHENSIVE</div>
      <div class="headline">Dental Care</div>
      <div class="subhead">FOR YOUR FAMILY</div>
      <div class="feature-pill">
        <span class="lead">with Modern Care &amp;</span>
        <span class="highlight">Advanced Technology</span>
      </div>
      <div class="phone">(555) 847-1390</div>
      <div class="website">www.harlowbrookdentistry.example</div>
    </div>
  </section>
</body>
</html>
```